Marlow Vale Stud website

We would like to create a horse stud/agistment farm website similar to this websites we have attached below:
www.thornbeck.com.au
www.quillstead.com.au
www.brackley.com
www.pimsey.com.au
The main colour scheme are purple and white to align with the stable's racing colours.
We have also attach the company logo and also images of the farm and create some ideas for the website.
Many thanks for looking into this project!

```html
<!DOCTYPE html>
<html lang="en">
<head>
<meta charset="utf-8">
<title>Marlow Vale Stud</title>
<link href="https://fonts.googleapis.com/css2?family=Poppins:wght@400;500;600;700&family=Roboto:wght@500;700;900&display=swap" rel="stylesheet">
<style>
:root{
  --purple:#4b1e5e;
  --purple-dark:#2f1239;
  --purple-mid:#6a3a80;
  --purple-soft:#8c5aa3;
  --ink:#1f1f1f;
  --grey:#7a7a7a;
  --line:#d9d2dd;
  --white:#ffffff;
  --footer:#1d1a1f;
  --grass:#5f7a3c;
  --sky:#9fb6c9;
  --earth:#7a5a3a;
}
*{box-sizing:border-box;margin:0;padding:0}
html,body{width:1200px;height:4612px;overflow:hidden;background:var(--white)}
body{position:relative;font-family:"Poppins",sans-serif;color:var(--ink)}
.abs{position:absolute}
h2.section-title{position:absolute;left:0;width:1200px;text-align:center;font-family:"Roboto",sans-serif;font-weight:700;font-size:44px;color:var(--ink);letter-spacing:.5px}
.btn{position:absolute;background:var(--purple);color:var(--white);font-size:15px;font-weight:500;letter-spacing:.5px;padding:8px 18px;text-transform:uppercase}
.para{font-size:14.5px;line-height:1.75;color:var(--grey)}
.photo{position:absolute}

/* header */
.site-header{position:absolute;left:0;top:0;width:1200px;height:112px;background:var(--white)}
.brand{position:absolute;left:108px;top:22px;display:flex;align-items:center;gap:14px}
.brand-dot{width:62px;height:62px;border-radius:50%;background:var(--purple)}
.brand-name{font-family:"Roboto",sans-serif;font-weight:700;font-size:34px;color:var(--purple)}
.topbar{position:absolute;right:112px;top:16px;display:flex;align-items:center;gap:26px;font-size:15px;color:var(--ink)}
.topbar .phone{font-weight:700;font-size:18px}
.topbar span{display:flex;align-items:center;gap:8px}
.socials{display:flex;gap:10px}
.socials i{width:14px;height:14px;border-radius:50%;background:var(--purple);display:block}
.main-nav{position:absolute;right:112px;top:72px;display:flex;gap:26px;font-size:14.5px;font-weight:500}
.main-nav a{color:var(--ink);text-decoration:none}
.main-nav a.active{font-weight:700;border-bottom:2px solid var(--purple);padding-bottom:4px}

/* hero */
.hero{position:absolute;left:0;top:112px;width:1200px;height:560px;background:linear-gradient(180deg,#8d9aa6 0%,#6a7560 40%,#3f4a2b 75%,#2c2a22 100%)}
.hero-title{position:absolute;left:0;top:318px;width:1200px;text-align:center;font-family:"Roboto",sans-serif;font-weight:700;font-size:58px;color:var(--white);letter-spacing:1px}
.hero-arrow{position:absolute;top:378px}
.hero-wings{position:absolute;left:0;top:600px}
.diamond{position:absolute;left:440px;top:540px;width:320px;height:320px;transform:rotate(45deg);border:8px solid var(--purple-soft);background:linear-gradient(135deg,#9cb2c4 0%,#7e9a6a 45%,#4e6e2e 100%);box-shadow:0 0 0 3px var(--white)}

/* about */
.about-mark{position:absolute;left:216px;top:842px;width:120px;height:120px;border-radius:50%;background:#efeaf1}
.about-text{position:absolute;left:185px;top:1046px;width:830px;text-align:center}

/* services */
.svc-card{position:absolute;top:1408px;width:312px;height:352px;border:1px solid var(--line);background:var(--white)}
.svc-img{position:absolute;left:6px;top:6px;width:298px;height:262px}
.svc-card h3{position:absolute;left:10px;top:290px;width:290px;text-align:center;font-size:16px;font-weight:600;color:var(--ink);line-height:1.3}
.svc-card p{position:absolute;left:20px;top:338px;width:270px;text-align:center;font-size:13px;color:var(--grey);line-height:1.5}
.svc-card{height:412px}
.svc-img{border-radius:0 0 150px 150px / 0 0 40px 40px}

/* news */
.news-img{position:absolute;width:456px;height:312px}
.date-tag{position:absolute;background:var(--purple);color:var(--white);font-weight:700;font-size:17px;padding:4px 14px}
.news-title{position:absolute;font-size:18px;font-weight:600;color:var(--purple)}
.news-text{position:absolute;width:460px}

/* contact band */
.contact-band{position:absolute;left:0;top:2900px;width:1200px;height:420px;background:linear-gradient(180deg,#3a1747 0%,#4f2462 50%,#3a1747 100%)}
.contact-band h2{color:var(--white);top:95px}
.contact-text{position:absolute;left:100px;top:172px;width:1000px;text-align:center;color:#e4d8ea}
.btn-outline{position:absolute;left:542px;top:330px;border:1px solid var(--white);color:var(--white);font-size:15px;padding:7px 16px}

/* gallery */
.g{position:absolute}

/* footer */
.site-footer{position:absolute;left:0;top:4180px;width:1200px;height:432px;background:var(--footer);color:var(--white)}
.site-footer h4{position:absolute;top:42px;font-family:"Roboto",sans-serif;font-weight:700;font-size:26px}
.f-contact{position:absolute;left:116px;top:104px;font-size:14.5px;line-height:1.5}
.f-contact div{display:flex;gap:14px;margin-bottom:22px;align-items:flex-start}
.f-links{position:absolute;left:540px;top:100px;list-style:none;font-size:15px;line-height:1.85}
.f-form{position:absolute;left:812px;top:102px;width:300px}
.f-form .field{background:#2d2a30;border:1px solid #3c3840;color:#9a96a0;font-size:13px;padding:9px 12px;height:40px}
.f-row{display:flex;gap:8px;margin-bottom:8px}
.f-row .field{flex:1}
.f-form .msg{height:40px;margin-bottom:10px}
.f-form .submit{display:inline-block;background:var(--purple);color:var(--white);font-size:14px;padding:8px 18px}
.copyright{position:absolute;left:0;top:394px;width:1200px;text-align:center;font-size:14px;color:#bdb8c2}
</style>
</head>
<body>

<header class="site-header">
  <div class="brand"><div class="brand-dot"></div><div class="brand-name">Marlow Vale Stud</div></div>
  <div class="topbar">
    <span class="phone">
      <svg width="16" height="16" viewBox="0 0 24 24"><path fill="#1f1f1f" d="M6.6 10.8a15 15 0 0 0 6.6 6.6l2.2-2.2a1 1 0 0 1 1-.25 11.4 11.4 0 0 0 3.6.6 1 1 0 0 1 1 1V20a1 1 0 0 1-1 1A17 17 0 0 1 3 4a1 1 0 0 1 1-1h3.5a1 1 0 0 1 1 1c0 1.25.2 2.45.6 3.6a1 1 0 0 1-.25 1z"/></svg>
      0390 555 0142</span>
    <span>
      <svg width="16" height="12" viewBox="0 0 24 18"><rect x="1" y="1" width="22" height="16" fill="none" stroke="#1f1f1f" stroke-width="2"/><path d="M1 1l11 9 11-9" fill="none" stroke="#1f1f1f" stroke-width="2"/></svg>
      hello@marlowvalestud.com</span>
    <div class="socials"><i></i><i></i><i></i></div>
  </div>
  <nav class="main-nav">
    <a class="active" href="#">HOME</a><a href="#">ABOUT</a><a href="#">STALLIONS</a><a href="#">FARM</a><a href="#">NEWS</a><a href="#">SERVICES</a><a href="#">CONTACT US</a>
  </nav>
</header>

<section class="hero" role="img" aria-label="Farm paddock with timber fencing and trees at dusk"></section>
<div class="hero-title">MARLOW VALE STUD</div>
<svg class="hero-arrow" style="left:26px" width="24" height="44" viewBox="0 0 24 44"><path d="M20 4L4 22l16 18" fill="none" stroke="#fff" stroke-width="4"/></svg>
<svg class="hero-arrow" style="right:26px" width="24" height="44" viewBox="0 0 24 44"><path d="M4 4l16 18L4 40" fill="none" stroke="#fff" stroke-width="4"/></svg>
<svg class="hero-wings" width="1200" height="220" viewBox="0 0 1200 220">
  <polygon points="0,60 1200,60 1200,120 600,210 0,120" fill="#3a1747"/>
  <polygon points="0,60 420,60 600,200 0,110" fill="#5a2a70" opacity=".7"/>
  <polygon points="1200,60 780,60 600,200 1200,110" fill="#5a2a70" opacity=".7"/>
</svg>
<div class="diamond" role="img" aria-label="Grey horse grazing in a green paddock"></div>

<section class="about">
  <div class="about-mark"></div>
  <h2 class="section-title" style="top:970px">About Us</h2>
  <p class="about-text para">Sed ut perspiciatis unde omnis iste natus error sit voluptatem accusantium doloremque laudantium, totam rem aperiam, eaque ipsa quae ab illo inventore veritatis et quasi architecto beatae vitae dicta sunt explicabo. Nemo enim ipsam voluptatem quia voluptas sit aspernatur aut odit aut fugit, sed quia.</p>
  <div class="btn" style="left:544px;top:1176px">Read More</div>
</section>

<section class="services">
  <h2 class="section-title" style="top:1302px">SERVICES</h2>
  <svg class="abs" style="left:58px;top:1616px" width="18" height="32" viewBox="0 0 18 32"><path d="M15 3L3 16l12 13" fill="none" stroke="#1f1f1f" stroke-width="4"/></svg>
  <svg class="abs" style="left:1116px;top:1616px" width="18" height="32" viewBox="0 0 18 32"><path d="M3 3l12 13L3 29" fill="none" stroke="#1f1f1f" stroke-width="4"/></svg>
  <article class="svc-card" style="left:112px">
    <div class="svc-img" role="img" aria-label="Young horse being led at a yearling sale" style="background:linear-gradient(160deg,#6b4a32,#3a2b22 60%,#7d8a5a)"></div>
    <h3>Weanling and Yearling<br>Sales Preparation</h3>
    <p>consectetur adipiscing elit, sed do eiusmod tempor</p>
  </article>
  <article class="svc-card" style="left:444px">
    <div class="svc-img" role="img" aria-label="Horse being handled during re-education work" style="background:linear-gradient(160deg,#8a6a4a,#5a4030 55%,#c9b79a)"></div>
    <h3>Breaking/ Re-education<br>of problem horses</h3>
    <p>consectetur adipiscing elit, sed do eiusmod tempor</p>
  </article>
  <article class="svc-card" style="left:776px">
    <div class="svc-img" role="img" aria-label="Bay horse standing in an agistment paddock" style="background:linear-gradient(160deg,#7a4a2a,#4a2c1a 55%,#8a9a6a)"></div>
    <h3>Agistment</h3>
    <p>all agistment services are available and can tailor to individual needs</p>
  </article>
</section>

<section class="news">
  <h2 class="section-title" style="top:1958px">NEWS</h2>
  <div class="news-img" role="img" aria-label="Grey horse galloping on a race track" style="left:112px;top:2068px;background:linear-gradient(180deg,#8a7a6a 0%,#c78a4a 35%,#4f7a3a 70%,#3a5a2a 100%)"></div>
  <div class="date-tag" style="left:112px;top:2076px">SEP 08</div>
  <div class="news-title" style="left:628px;top:2070px">At vero eos et accusamus et iusto</div>
  <p class="news-text para" style="left:628px;top:2114px">Qui blanditiis praesentium voluptatum deleniti atque corrupti quos dolores et quas molestias excepturi sint occaecati cupiditate non provident, similique sunt in culpa qui officia deserunt mollitia animi, id est laborum et dolorum fuga. Et harum quidem rerum facilis est et expedita distinctio. Nam libero tempore, cum soluta nobis</p>
  <div class="btn" style="left:628px;top:2334px">Read More</div>

  <div class="news-title" style="left:112px;top:2472px">Quis nostrud exercitation ullamco laboris</div>
  <p class="news-text para" style="left:112px;top:2516px">Qui blanditiis praesentium voluptatum deleniti atque corrupti quos dolores et quas molestias excepturi sint occaecati cupiditate non provident, similique sunt in culpa qui officia deserunt mollitia animi, id est laborum et dolorum fuga. Et harum quidem rerum facilis est et expedita distinctio. Nam libero tempore, cum soluta nobis</p>
  <div class="btn" style="left:112px;top:2738px">Read More</div>
  <div class="news-img" role="img" aria-label="Group of horses standing in a paddock under blue sky" style="left:628px;top:2468px;background:linear-gradient(180deg,#5a8ac9 0%,#a9c6e6 45%,#6a8a3a 70%,#4a6a2a 100%)"></div>
  <div class="date-tag" style="left:1004px;top:2476px">OCT 20</div>
</section>

<section class="contact-band" role="img" aria-label="Purple-tinted aerial view of the stables">
  <h2 class="section-title">CONTACT US</h2>
  <p class="contact-text para" style="color:#e4d8ea">vero eos et accusamus et iusto odio dignissimos ducimus qui blanditiis praesentium voluptatum deleniti atque corrupti quos dolores et quas molestias excepturi sint occaecati cupiditate non provident, similique sunt in culpa qui officia deserunt mollitia animi, id est laborum et dolorum fuga. Et harum quidem rerum facilis est et expedita distinctio. Nam libero tempore, cum soluta nobis est eligendi optio</p>
  <div class="btn-outline">READ MORE</div>
</section>

<section class="gallery">
  <h2 class="section-title" style="top:3470px">GALLERY</h2>
  <div class="g" role="img" aria-label="Aerial view of the farm buildings and paddocks" style="left:112px;top:3560px;width:456px;height:220px;background:linear-gradient(150deg,#7a9a5a,#4a6a3a 55%,#9a8a6a)"></div>
  <div class="g" role="img" aria-label="Horses grazing in a green field" style="left:584px;top:3560px;width:276px;height:220px;background:linear-gradient(180deg,#c9d6e0,#6a9a4a 55%,#4a7a2a)"></div>
  <div class="g" role="img" aria-label="Tree-lined gravel driveway" style="left:876px;top:3560px;width:212px;height:448px;background:linear-gradient(180deg,#dfe6ee 0%,#3a5a2a 35%,#c9a87a 100%)"></div>
  <div class="g" role="img" aria-label="Mare and foal under a large tree" style="left:112px;top:3796px;width:268px;height:212px;background:linear-gradient(180deg,#b9c9d6,#5a7a3a 55%,#3a5a2a)"></div>
  <div class="g" role="img" aria-label="Timber fenced paddock at sunset" style="left:392px;top:3796px;width:268px;height:212px;background:linear-gradient(180deg,#e0a86a,#7a5a3a 50%,#4a5a2a)"></div>
  <div class="g" role="img" aria-label="Chestnut horse standing on grass" style="left:672px;top:3796px;width:188px;height:212px;background:linear-gradient(180deg,#dfe6ee,#a86a3a 50%,#6a8a3a)"></div>
  <div class="btn" style="left:516px;top:4076px;font-size:14px">View More Images</div>
</section>

<footer class="site-footer">
  <h4 style="left:116px">Contact Info</h4>
  <div class="f-contact">
    <div><svg width="14" height="18" viewBox="0 0 14 18"><path d="M7 0a7 7 0 0 0-7 7c0 5 7 11 7 11s7-6 7-11a7 7 0 0 0-7-7zm0 9.5A2.5 2.5 0 1 1 7 4.5a2.5 2.5 0 0 1 0 5z" fill="#fff"/></svg><span>Lorem ipsum dolor sit amet,<br>consectetur adipiscing elit,</span></div>
    <div><svg width="14" height="14" viewBox="0 0 24 24"><path fill="#fff" d="M6.6 10.8a15 15 0 0 0 6.6 6.6l2.2-2.2a1 1 0 0 1 1-.25 11.4 11.4 0 0 0 3.6.6 1 1 0 0 1 1 1V20a1 1 0 0 1-1 1A17 17 0 0 1 3 4a1 1 0 0 1 1-1h3.5a1 1 0 0 1 1 1c0 1.25.2 2.45.6 3.6a1 1 0 0 1-.25 1z"/></svg><span>0390 555 0142</span></div>
    <div><svg width="16" height="12" viewBox="0 0 24 18"><rect x="1" y="1" width="22" height="16" fill="none" stroke="#fff" stroke-width="2"/><path d="M1 1l11 9 11-9" fill="none" stroke="#fff" stroke-width="2"/></svg><span>hello@marlowvalestud.com</span></div>
  </div>
  <h4 style="left:540px">Links</h4>
  <ul class="f-links"><li>HOME</li><li>ABOUT</li><li>STALLIONS</li><li>FARM</li><li>NEWS</li></ul>
  <h4 style="left:812px">Contact Form</h4>
  <div class="f-form">
    <div class="f-row"><div class="field">Name</div><div class="field">Email</div></div>
    <div class="field msg">Message</div>
    <div class="submit">Submit</div>
  </div>
  <div class="copyright">© Marlowvalestud 2018 All Rights Reserved</div>
</footer>

</body>
</html>
```